Postcard Design for Birchwell Medical Center Integrated Medicine

We need a postcard that we will be able to hand out at events that gives an overview of what we do at Birchwell Medical Center. Birchwell Medical Center, located in Encinitas, California, is an integrated medical center using functional medicine to prevent and reverse chronic diseases. We would also like to highly emphasize that we take Senivex and PPO insurance for these services and if patients have any questions to contact the front desk.

The attached screenshots are elementary versions of what we hope our postcard will have.

THIS IS NOT INTENDED TO BE MAILED SO AN ADDRESS SPACE IS NOT NEEDED
ALSO, WE WOULD LIKE TO HAVE THIS SIZE 6X4

Birchwellmedicalcenter.net is our website if you would need any further information about the company.

```html
<!DOCTYPE html>
<html lang="en">
<head>
<meta charset="utf-8">
<title>Birchwell Medical Center Integrated Medicine – Postcard</title>
<link rel="stylesheet" href="https://fonts.googleapis.com/css2?family=Arimo:wght@400;700&display=swap">
<style>
  :root {
    --ink: #111111;
    --halo: #ffffff;
    --panel: #ffffff;
    --skin-light: #e9c2ad;
    --skin-mid: #d98a62;
    --skin-deep: #a9532c;
    --backdrop-pale: #ece6e4;
    --backdrop-warm: #c46a3e;
    --towel: #d8707c;
  }
  html, body {
    margin: 0;
    padding: 0;
    overflow: hidden;
    background: #ffffff;
  }
  .postcard {
    position: relative;
    width: 1200px;
    height: 930px;
    overflow: hidden;
    font-family: "Arimo", Arial, sans-serif;
    color: var(--ink);
  }
  .postcard__photo {
    position: absolute;
    inset: 0;
    background:
      linear-gradient(180deg, transparent 0%, transparent 80%, var(--towel) 88%, #b8515f 100%),
      radial-gradient(ellipse 55% 45% at 72% 48%, var(--skin-mid) 0%, transparent 70%),
      radial-gradient(ellipse 60% 50% at 20% 30%, var(--backdrop-pale) 0%, transparent 70%),
      linear-gradient(100deg, var(--skin-light) 0%, var(--skin-mid) 45%, var(--backdrop-warm) 75%, var(--skin-deep) 100%);
  }
  .postcard__intro {
    position: absolute;
    left: 43px;
    top: 50px;
    width: 860px;
    margin: 0;
    font-size: 28px;
    font-weight: 700;
    line-height: 38.5px;
  }
  .conditions {
    position: absolute;
    top: 253px;
    margin: 0;
    padding: 0;
    list-style: none;
    font-size: 26px;
    line-height: 35.7px;
    text-shadow:
      1.5px 0 0 var(--halo), -1.5px 0 0 var(--halo),
      0 1.5px 0 var(--halo), 0 -1.5px 0 var(--halo),
      1px 1px 0 var(--halo), -1px -1px 0 var(--halo),
      1px -1px 0 var(--halo), -1px 1px 0 var(--halo);
  }
  .conditions--left { left: 38px; width: 280px; }
  .conditions--right { left: 428px; width: 400px; }
  .postcard__insurance {
    position: absolute;
    left: 42px;
    top: 655px;
    margin: 0;
    font-size: 26px;
    font-weight: 700;
    line-height: 37px;
  }
  .panel {
    position: absolute;
    background: var(--panel);
  }
  .panel--logo { left: 903px; top: 29px; width: 268px; height: 268px; }
  .panel--footer { left: 151px; top: 766px; width: 1019px; height: 133px; }
</style>
</head>
<body>
<main class="postcard">
  <div class="postcard__photo" role="img" aria-label="Photograph of hands resting on a patient's back during a massage, on a pink towel"></div>

  <p class="postcard__intro">Treating root causes not symptoms by using a whole system approach to medicine, preventing and reversing chronic condition and disease. Ultimately, creating optimal health and vitality. Some of the conditions we treat are...</p>

  <ul class="conditions conditions--left">
    <li>Acne</li>
    <li>Diabetes</li>
    <li>Depression/Anxiety</li>
    <li>Healthy Aging</li>
    <li>Parkinson’s Disease</li>
    <li>Sleep Insomnia</li>
    <li>Healthy Weight and Metabolism</li>
    <li>Cancer Prevention</li>
    <li>Thyroid/Adrenal Disorders</li>
  </ul>

  <ul class="conditions conditions--right">
    <li>Arthritis</li>
    <li>Asthma</li>
    <li>Detoxification and Healing</li>
    <li>Migraines and Headaches</li>
    <li>Chronic Fatugue</li>
    <li>Autoimmune Diseases</li>
    <li>Food Allergies</li>
    <li>Female Disorders</li>
    <li>Hormone Imbalance</li>
    <li>Osteoporosis</li>
    <li>And many more</li>
  </ul>

  <p class="postcard__insurance">we accept all Senivex and PPO insurance<br>Please contact the front desk for more<br>information</p>

  <div class="panel panel--logo"></div>
  <div class="panel panel--footer"></div>
</main>
</body>
</html>
```